Super elegant, crisp & clean Business card design required

We recently upgraded our branding - which is on our website - talvendoraphoto.com

I would like a simple, yet elegant, clean business card design please.

The font of my logo is Cinzel - and because of the natural colour - it's best to have this on a black background.

I would like to have the back of the business card - with simply my logo.

PLEASE DO NOT SUBMIT A COMPLICATED / UNCLEAN DESIGN

Industry/Entity Type

Business

Contact Information for Business Card

Talven Doroshko Photography

Font styles to use
Other font styles liked:
• Cinzel

Requirements
Must have
• A backpage with nothing but my logo
• Simple design - stands out
Should not have
• Colour that dont align with my logo
• Over complicated '/ non symmetrical design

```html
<!DOCTYPE html>
<html lang="en">
<head>
<meta charset="utf-8">
<title>Talven Doroshko Photography – Business Card</title>
<link href="https://fonts.googleapis.com/css2?family=Cinzel:wght@400&family=Source+Sans+3:wght@400&display=swap" rel="stylesheet">
<style>
  :root {
    --stage: #000000;
    --card: #333436;
    --gold: #a38d6b;
    --text: #f2f2f2;
    --icon: #9a9a9a;
    --rule: #45464a;
  }
  html, body {
    margin: 0;
    padding: 0;
    width: 1200px;
    height: 900px;
    overflow: hidden;
    background: var(--stage);
  }
  .canvas {
    position: relative;
    width: 1200px;
    height: 900px;
  }
  .card {
    position: absolute;
    top: 271px;
    width: 456px;
    height: 281px;
    border-radius: 14px;
    background: var(--card);
  }
  .card--front { left: 137px; }
  .card--back { left: 627px; }

  .front-brand {
    position: absolute;
    left: 28px;
    top: 110px;
    width: 150px;
    text-align: center;
    font-family: "Cinzel", serif;
    font-weight: 400;
    font-size: 17px;
    line-height: 1.35;
    color: var(--gold);
    letter-spacing: 0.04em;
  }
  .divider {
    position: absolute;
    left: 194px;
    top: 64px;
    width: 1px;
    height: 176px;
    background: var(--rule);
  }
  .details {
    position: absolute;
    left: 217px;
    top: 62px;
    font-family: "Source Sans 3", sans-serif;
    color: var(--text);
  }
  .details__name {
    margin: 0;
    font-size: 17px;
    line-height: 22px;
    color: var(--gold);
    font-weight: 400;
  }
  .details__role {
    margin: 0 0 16px;
    font-size: 13px;
    line-height: 15px;
  }
  .details__address {
    margin: 0 0 14px;
    font-size: 13px;
    line-height: 14px;
    font-style: normal;
  }
  .contact-list {
    list-style: none;
    margin: 0;
    padding: 0;
    font-size: 13px;
  }
  .contact-list li {
    display: flex;
    align-items: center;
    height: 19px;
  }
  .contact-list svg {
    width: 9px;
    height: 9px;
    margin-right: 8px;
    fill: var(--icon);
  }

  .back-brand {
    position: absolute;
    left: 0;
    right: 0;
    top: 160px;
    text-align: center;
    font-family: "Cinzel", serif;
    font-weight: 400;
    color: var(--gold);
  }
  .back-brand__mark {
    display: block;
    margin: 0 auto 14px;
    width: 10px;
    height: 10px;
    border-radius: 50%;
    background: var(--gold);
  }
  .back-brand__name {
    display: block;
    font-size: 21px;
    letter-spacing: 0.03em;
    line-height: 24px;
  }
  .back-brand__sub {
    display: block;
    font-size: 10px;
    letter-spacing: 0.55em;
    line-height: 14px;
    padding-left: 0.55em;
  }
</style>
</head>
<body>
<main class="canvas">
  <section class="card card--front" aria-label="Business card front">
    <div class="front-brand">Talven<br>Doroshko</div>
    <div class="divider"></div>
    <div class="details">
      <h1 class="details__name">Arlen Vesko</h1>
      <p class="details__role">Managing Director</p>
      <address class="details__address">12345, Address Goes Here<br>Country Name, 123456</address>
      <ul class="contact-list">
        <li>
          <svg viewBox="0 0 10 10" aria-hidden="true"><path d="M2 0.5 L3.6 0.5 L4.2 2.8 L3.1 3.7 Q4.2 5.9 6.3 6.9 L7.2 5.8 L9.5 6.4 L9.5 8 Q9.3 9.5 7.8 9.5 Q0.5 8.8 0.5 2.2 Q0.5 0.7 2 0.5 Z"/></svg>
          (044)-456-7890
        </li>
        <li>
          <svg viewBox="0 0 10 10" aria-hidden="true"><path d="M2.5 0.5 H7.5 V3 H9.5 V9.5 H0.5 V3 H2.5 Z M3.5 1.5 V3 H6.5 V1.5 Z M2 5 V6 H3 V5 Z M4.5 5 V6 H5.5 V5 Z M7 5 V6 H8 V5 Z"/></svg>
          123-456-7890
        </li>
        <li>
          <svg viewBox="0 0 10 10" aria-hidden="true"><path d="M0.5 2 H9.5 V8.5 H0.5 Z M1.2 2.6 L5 5.6 L8.8 2.6 Z" fill-rule="evenodd"/></svg>
          info@youremail.com
        </li>
        <li>
          <svg viewBox="0 0 10 10" aria-hidden="true"><circle cx="5" cy="5" r="4.5"/></svg>
          www.talvendoraphoto.com
        </li>
      </ul>
    </div>
  </section>

  <section class="card card--back" aria-label="Business card back">
    <div class="back-brand">
      <span class="back-brand__mark"></span>
      <span class="back-brand__name">Talven Doroshko</span>
      <span class="back-brand__sub">PHOTOGRAPHY</span>
    </div>
  </section>
</main>
</body>
</html>
```